Maplecrest Disability - Social Security Disability Attorneys

Our company is expanding to attract clients nationwide for our social security disability practice. We have a logo, but I am looking for a creative and elegant letterhead that projects an image of being technologically advanced but still professional enough for the legal field. I am looking for the "wow factor" combined with this is still professional enough for a law practice.

Requesting letterhead and business card design
Updates

Had to update and change the logo. The previous logo had a typo. Please send updates with the new logo for consideration. The letterhead and business cards should be professional enough to be used for a law firm. Thanks.

Industry/Entity Type

Law Practice, Law Firm, Healthcare Industry, Government

Colors

Designer to choose colors to be used in the design.

Requirements
Nice to have
• **Please create a vertical design for the business card**

```html
<!DOCTYPE html>
<html lang="en">
<head>
<meta charset="utf-8">
<title>Maplecrest Disability – Business Card</title>
<link rel="stylesheet" href="https://fonts.googleapis.com/css2?family=Cinzel:wght@500&family=Montserrat:wght@400;700&display=swap">
<style>
  :root {
    --backdrop: #219dd9;
    --card: #171717;
    --accent: #f5862a;
    --brand-blue: #5366b3;
    --ink-light: #f2f2f2;
  }
  * { margin: 0; padding: 0; box-sizing: border-box; }
  html, body { width: 1200px; height: 1128px; overflow: hidden; }
  body {
    position: relative;
    background: var(--backdrop);
    font-family: "Montserrat", Arial, sans-serif;
    color: var(--ink-light);
  }
  .card {
    position: absolute;
    top: 129px;
    width: 499px;
    height: 870px;
    background: var(--card);
    border-radius: 44px;
    box-shadow: 0 18px 40px rgba(0, 0, 0, 0.45);
    overflow: hidden;
  }
  .card--front { left: 71px; }
  .card--back { left: 633px; width: 496px; }

  /* Front: vertical brand lockup */
  .brand-vertical {
    position: absolute;
    left: 270px;
    top: 433px;
    width: 900px;
    transform: translate(-50%, -50%) rotate(-90deg);
    display: flex;
    flex-direction: column;
    align-items: center;
  }
  .brand-vertical__name {
    font-family: "Cinzel", Georgia, serif;
    font-weight: 500;
    font-size: 43px;
    letter-spacing: 1px;
    line-height: 1;
    color: var(--ink-light);
    white-space: nowrap;
  }
  .brand-vertical__tagline {
    margin-top: 14px;
    font-family: "Cinzel", Georgia, serif;
    font-weight: 500;
    font-size: 15px;
    letter-spacing: 6.6px;
    line-height: 1;
    color: var(--ink-light);
    white-space: nowrap;
  }
  .brand-dot {
    position: absolute;
    border-radius: 50%;
    background: var(--accent);
  }
  .card--front .brand-dot { left: 160px; top: 414px; width: 38px; height: 38px; }

  /* Back */
  .card--back .brand-dot { left: 236px; top: 148px; width: 24px; height: 24px; }
  .brand-horizontal {
    position: absolute;
    left: 0; right: 0;
    top: 178px;
    text-align: center;
    color: var(--brand-blue);
    font-family: "Cinzel", Georgia, serif;
    font-weight: 500;
  }
  .brand-horizontal__name {
    font-size: 29px;
    letter-spacing: 1px;
    line-height: 1;
    white-space: nowrap;
  }
  .brand-horizontal__tagline {
    margin-top: 9px;
    font-size: 9.5px;
    letter-spacing: 2.6px;
    white-space: nowrap;
  }
  .person {
    position: absolute;
    left: 0; right: 0;
    top: 309px;
    text-align: center;
  }
  .person__name {
    font-weight: 700;
    font-size: 29px;
    color: var(--accent);
    letter-spacing: -0.3px;
    line-height: 1;
  }
  .person__role {
    margin-top: 11px;
    display: flex;
    align-items: center;
    justify-content: center;
    gap: 6px;
    font-size: 20px;
    line-height: 1;
  }
  .person__role::before,
  .person__role::after {
    content: "";
    width: 66px;
    height: 2px;
    background: linear-gradient(90deg, transparent, var(--accent));
  }
  .person__role::after { background: linear-gradient(90deg, var(--accent), transparent); }
  .address {
    position: absolute;
    left: 0; right: 0;
    top: 447px;
    text-align: center;
    font-size: 18.5px;
    line-height: 29px;
    font-style: normal;
  }
  .contact-icons {
    position: absolute;
    left: 0; right: 0;
    top: 549px;
    display: flex;
    justify-content: center;
    gap: 34px;
  }
  .contact-icons svg { width: 22px; height: 22px; fill: var(--accent); }
  .contact-rule {
    position: absolute;
    left: 177px;
    width: 139px;
    top: 590px;
    height: 2px;
    background: var(--accent);
  }
  .contact-list {
    position: absolute;
    left: 0; right: 0;
    top: 606px;
    list-style: none;
    text-align: center;
    font-size: 19px;
    line-height: 33px;
  }
</style>
</head>
<body>
  <section class="card card--front" aria-label="Card front">
    <span class="brand-dot" aria-hidden="true"></span>
    <div class="brand-vertical">
      <div class="brand-vertical__name">MAPLECREST DISABILITY</div>
      <div class="brand-vertical__tagline">SOCIAL SECURITY DISABILITY ATTORNEYS</div>
    </div>
  </section>

  <section class="card card--back" aria-label="Card back">
    <span class="brand-dot" aria-hidden="true"></span>
    <div class="brand-horizontal">
      <div class="brand-horizontal__name">MAPLECREST DISABILITY</div>
      <div class="brand-horizontal__tagline">SOCIAL SECURITY DISABILITY ATTORNEYS</div>
    </div>

    <div class="person">
      <div class="person__name">DANIEL WHITCOMBE</div>
      <div class="person__role">Co-Founder</div>
    </div>

    <address class="address">Suite 4, Level 12, Harbour<br>Street Sydney NSW 2000</address>

    <div class="contact-icons" aria-hidden="true">
      <svg viewBox="0 0 24 24"><path d="M6.6 10.8a15.1 15.1 0 0 0 6.6 6.6l2.2-2.2a1 1 0 0 1 1-.25 11.4 11.4 0 0 0 3.6.57 1 1 0 0 1 1 1V20a1 1 0 0 1-1 1A17 17 0 0 1 3 4a1 1 0 0 1 1-1h3.5a1 1 0 0 1 1 1c0 1.25.2 2.45.57 3.57a1 1 0 0 1-.25 1z"/></svg>
      <svg viewBox="0 0 24 24"><path d="M2 5h20v14H2z M3.5 6.5 12 13l8.5-6.5" stroke="#171717" stroke-width="1.5"/></svg>
      <svg viewBox="0 0 24 24"><circle cx="12" cy="12" r="10"/><path d="M2 12h20M12 2c3 3 3 17 0 20M12 2c-3 3-3 17 0 20" stroke="#171717" stroke-width="1.4" fill="none"/></svg>
    </div>
    <div class="contact-rule"></div>
    <ul class="contact-list">
      <li>555-014-2286</li>
      <li>info@maplecrestdisability.com</li>
      <li>www.maplecrestdisability.com</li>
    </ul>
  </section>
</body>
</html>
```